A parent Company needs a website as a leading diversified business in industrial Conglomerates in Af

Velkor Group is a private (Holding) limited liability company incorporated under the Companies Code, 1963 (Act 179) in November, 2013 to following the speedy growth in numbers of its current subsidiaries which has been founded several years ago with an emerging force to become one of the largest and a leading diversified business in industrial Conglomerates in Africa.
The Group which is 100% wholly owned indigenous Ghanaian Company focuses on provision of local, value-added products and services that meet the needs of the African population. The Group is headquartered in Accra, Ghana with interests across a range of sectors in Africa.
We are currently into Food & Beverage, Real Estate Development, Transportation, Health Care, Consumer Products Distribution, Agro Processing, Manufacturing, ICT, Exports & Import, and still counting.
In the next 3 years, we shall announce our ambitions to enter Ghana's largest Oil and Gas industry, playing a strategic role in the petroleum sector with strategic alliances, and help build Ghana's biggest and most important Energy sector in the country.
Inspired by billionaires Tom Prewitt, Harlan Voskel, and Emeka Ofodile, Velkor Group (Velkor Foundation) is committed to making a name for itself on the philanthropic circuit and has given away privately and still given to the cause to the needy in the society and some specific social causes in Ghana.
The company is managed by a 5 member board and a 2 member advisory experts who are non-board members.
The company has a vision, mission and it is guided by its core values.
We would like to see a designs that is very professional and looks corporate and can attract investors and partners. It must communicate financial safety and growth and must reflect our logo colors.

```html
<!DOCTYPE html>
<html lang="en">
<head>
<meta charset="utf-8">
<title>Velkor Group</title>
<link href="https://fonts.googleapis.com/css2?family=Arimo:wght@400;700&display=swap" rel="stylesheet">
<style>
:root{
  --blue:#0a68b4;
  --blue-dark:#075a9e;
  --red:#d8232a;
  --text:#333;
  --muted:#8a8a8a;
  --line:#d9d9d9;
  --panel:#f4f4f4;
  --white:#fff;
}
*{box-sizing:border-box;margin:0;padding:0}
html,body{width:725px;height:1200px;overflow:hidden;background:var(--white);font-family:"Arimo",Arial,sans-serif;color:var(--text)}
.page{position:relative;width:725px;height:1200px}
.abs{position:absolute}

/* header */
.brand{left:80px;top:14px;display:flex;align-items:center;gap:7px}
.brand-mark{width:22px;height:22px;border-radius:50%;background:var(--blue)}
.brand-name{font-size:14px;font-weight:700;color:var(--blue)}
.account{left:474px;top:14px;font-size:7px;color:#555}
.social{left:552px;top:11px;display:flex;gap:5px}
.social span{width:15px;height:15px;border:1px solid #bbb;border-radius:2px}
.call{left:386px;top:43px;font-size:7px;color:#555}
.call b{font-size:12px;font-weight:400;color:var(--blue)}
.search{left:510px;top:38px;width:116px;height:18px;border:1px solid #ddd;font-size:6px;color:#999;padding:5px 4px}
.search-btn{left:630px;top:38px;width:17px;height:17px;border-radius:50%;background:var(--red)}

.nav{left:0;top:66px;width:725px;height:28px;background:var(--blue)}
.nav a{color:var(--white);font-size:10.5px;text-decoration:none;position:absolute;top:9px}

.hero{left:0;top:94px;width:725px;height:256px;background:linear-gradient(180deg,#cfdbe8 0%,#8fa6c2 55%,#2c3447 100%)}
.dots{left:80px;top:275px;display:flex;gap:7px}
.dots span{width:12px;height:12px;border-radius:50%;border:2px solid var(--blue)}
.dots span.on{border-color:var(--red)}

/* services */
.service{width:133px;height:184px;border:1px solid var(--line);text-align:center}
.service svg{margin-top:7px}
.service .rule{width:58px;height:2px;background:var(--blue);margin:5px auto 9px}
.service h3{font-size:9px;font-weight:400;color:var(--red);line-height:14px;height:28px}
.service p{font-size:6px;color:#999;line-height:14px}
.btn{display:inline-block;background:var(--blue);color:var(--white);font-size:7.5px;padding:6px 0;width:80px;margin-top:8px;border:1px solid var(--blue-dark)}

/* sidebar */
.events{left:512px;top:369px;width:134px}
.events h2{font-size:10px;font-weight:400;color:var(--blue);padding-bottom:6px;border-bottom:1px solid var(--line)}
.event{display:flex;gap:6px;padding:9px 0 10px;border-bottom:1px dotted #ccc;height:66px}
.thumb{width:47px;height:43px;flex:none}
.event .date{font-size:7px;color:var(--red)}
.event .title{font-size:6.3px;color:#444;line-height:10px;margin-top:3px}
.event .ago{font-size:6px;color:#999}
.more{left:566px;top:729px;width:80px;height:20px;background:#9a9a9a;color:var(--white);font-size:7.5px;text-align:center;line-height:20px}

/* welcome */
.welcome{left:79px;top:772px;width:567px;height:223px;border:1px solid var(--line);background:var(--panel);text-align:center}
.welcome h2{font-size:14px;font-weight:400;color:var(--blue);line-height:18px;margin-top:10px}
.feature{position:absolute;top:54px;width:175px;text-align:center}
.feature .img{height:72px;border:3px solid #ddd}
.feature h3{font-size:9px;font-weight:400;color:var(--red);margin-top:11px}
.feature p{font-size:6.3px;color:#555;line-height:10px;margin-top:6px}
.feature a{display:block;font-size:6px;color:var(--blue);margin-top:6px;text-decoration:none}

/* footer */
.footer{left:0;top:1018px;width:725px;height:182px;background:var(--blue);color:var(--white)}
.fcol{position:absolute;top:14px}
.fcol h4{font-size:10px;font-weight:400;padding-bottom:8px;border-bottom:1px solid #2d7fc2;width:120px}
.grid{display:grid;grid-template-columns:repeat(3,35px);gap:4px;margin-top:9px}
.grid span{height:28px}
.news{font-size:6.5px;line-height:10px}
.fbtn{display:inline-block;background:var(--red);color:var(--white);font-size:6.5px;padding:3px 10px}
.input{width:120px;height:15px;background:var(--white);margin-top:5px}
.copy{left:0;top:160px;width:725px;text-align:center;font-size:6.5px;border-top:1px solid #2d7fc2;padding-top:10px}
</style>
</head>
<body>
<div class="page">

  <div class="abs brand"><span class="brand-mark"></span><span class="brand-name">Velkor Group</span></div>
  <div class="abs account">My Account &nbsp;|&nbsp; Login</div>
  <div class="abs social"><span></span><span></span><span></span><span></span><span></span></div>
  <div class="abs call">Call us: <b>1-800-555-0142</b></div>
  <div class="abs search">Search......</div>
  <div class="abs search-btn">
    <svg width="17" height="17" viewBox="0 0 17 17"><circle cx="7.5" cy="7.5" r="3" fill="none" stroke="#fff" stroke-width="1.4"/><line x1="9.7" y1="9.7" x2="12.5" y2="12.5" stroke="#fff" stroke-width="1.6"/></svg>
  </div>

  <nav class="abs nav">
    <a style="left:79px">HOME</a>
    <a style="left:165px">ABOUT US</a>
    <a style="left:277px">SERVICES</a>
    <a style="left:385px">PRODUCTS</a>
    <a style="left:493px">BLOG</a>
    <a style="left:581px">CONTACT US</a>
  </nav>

  <div class="abs hero" role="img" aria-label="Three business professionals in suits standing in a bright glass atrium"></div>
  <div class="abs dots"><span></span><span class="on"></span><span></span><span></span></div>

  <div class="abs service" style="left:79px;top:371px">
    <svg width="56" height="50" viewBox="0 0 56 50"><path d="M4 28h40l-4 10H10z" fill="#555"/><rect x="46" y="10" width="3" height="34" fill="#555"/><rect x="42" y="12" width="2" height="16" fill="#555"/><path d="M14 26c2-8 20-8 22 0" fill="none" stroke="#555" stroke-width="2"/></svg>
    <div class="rule"></div><h3>Food &amp; Beverage</h3>
    <p>Accredited for use under the RCE<br>Energy Saving Scheme, making it<br>eligible for massiv</p>
    <span class="btn">Read More &gt;&gt;</span>
  </div>
  <div class="abs service" style="left:223px;top:371px">
    <svg width="56" height="50" viewBox="0 0 56 50"><rect x="20" y="6" width="6" height="40" fill="#555"/><rect x="27" y="4" width="6" height="42" fill="#444"/><rect x="34" y="8" width="4" height="36" fill="#666"/></svg>
    <div class="rule"></div><h3>Real Estate Development</h3>
    <p>Accredited for use under the RCE<br>Energy Saving Scheme, making it<br>eligible for massiv</p>
    <span class="btn">Read More &gt;&gt;</span>
  </div>
  <div class="abs service" style="left:367px;top:371px">
    <svg width="56" height="50" viewBox="0 0 56 50"><rect x="8" y="10" width="26" height="26" rx="2" fill="none" stroke="#555" stroke-width="3"/><path d="M34 18h9l6 9v9H34z" fill="none" stroke="#555" stroke-width="3"/><circle cx="18" cy="39" r="5" fill="#fff" stroke="#555" stroke-width="3"/><circle cx="40" cy="39" r="5" fill="#fff" stroke="#555" stroke-width="3"/></svg>
    <div class="rule"></div><h3>Transportation</h3>
    <p>Accredited for use under the RCE<br>Energy Saving Scheme, making it<br>eligible for ma</p>
    <span class="btn">Read More &gt;&gt;</span>
  </div>

  <div class="abs service" style="left:79px;top:566px">
    <svg width="56" height="50" viewBox="0 0 56 50"><rect x="20" y="6" width="16" height="8" rx="2" fill="none" stroke="#555" stroke-width="3"/><rect x="10" y="12" width="36" height="30" rx="3" fill="#555"/><rect x="25" y="18" width="6" height="18" fill="#fff"/><rect x="19" y="24" width="18" height="6" fill="#fff"/></svg>
    <div class="rule"></div><h3>Health Care</h3>
    <p>Accredited for use under the RCE<br>Energy Saving Scheme, making it<br>eligible for massiv</p>
    <span class="btn">Read More &gt;&gt;</span>
  </div>
  <div class="abs service" style="left:223px;top:566px">
    <svg width="56" height="50" viewBox="0 0 56 50"><circle cx="28" cy="16" r="9" fill="#555"/><path d="M10 44c0-12 8-17 18-17s18 5 18 17z" fill="#555"/></svg>
    <div class="rule"></div><h3>Consumer Products<br>Distribution</h3>
    <p>Energy Saving Scheme, making it<br>eligible for massiv</p>
    <span class="btn">Read More &gt;&gt;</span>
  </div>
  <div class="abs service" style="left:367px;top:566px">
    <svg width="56" height="50" viewBox="0 0 56 50"><circle cx="22" cy="28" r="10" fill="none" stroke="#555" stroke-width="7" stroke-dasharray="4 3"/><circle cx="22" cy="28" r="5" fill="#555"/><circle cx="38" cy="14" r="6" fill="none" stroke="#555" stroke-width="5" stroke-dasharray="3 2"/></svg>
    <div class="rule"></div><h3>Agro Processing</h3>
    <p>Accredited for use under the RCE<br>Energy Saving Scheme, making it<br>eligible for ma</p>
    <span class="btn">Read More &gt;&gt;</span>
  </div>

  <aside class="abs events">
    <h2>Recent Events</h2>
    <div class="event"><div class="thumb" role="img" aria-label="Plated food dishes" style="background:linear-gradient(135deg,#e9d9b8,#c55a2a)"></div><div><div class="date">Thursday, 9 Jan, 19:00</div><div class="title">Reel Movie Club: "Harbor<br>Lights"</div><div class="ago">2 days ago</div></div></div>
    <div class="event"><div class="thumb" role="img" aria-label="Group of staff standing in an office" style="background:linear-gradient(135deg,#d6dbe0,#4b5563)"></div><div><div class="date">Thursday, 9 Jan, 19:00</div><div class="title">Reel Movie Club: "Harbor<br>Lights"</div><div class="ago">2 days ago</div></div></div>
    <div class="event"><div class="thumb" role="img" aria-label="House against a mountain landscape" style="background:linear-gradient(180deg,#8bb7e0,#6b5a40)"></div><div><div class="date">Thursday, 9 Jan, 19:00</div><div class="title">Reel Movie Club: "Harbor<br>Lights"</div><div class="ago">2 days ago</div></div></div>
    <div class="event"><div class="thumb" role="img" aria-label="Passenger train at a platform" style="background:linear-gradient(180deg,#cfd6de,#6e7780)"></div><div><div class="date">Thursday, 9 Jan, 19:00</div><div class="title">Reel Movie Club: "Harbor<br>Lights"</div><div class="ago">2 days ago</div></div></div>
    <div class="event"><div class="thumb" role="img" aria-label="Portrait of a smiling woman" style="background:linear-gradient(135deg,#9ccde0,#d9b48a)"></div><div><div class="date">Thursday, 9 Jan, 19:00</div><div class="title">Reel Movie Club: "Harbor<br>Lights"</div><div class="ago">2 days ago</div></div></div>
  </aside>
  <div class="abs more">View More &gt;&gt;</div>

  <section class="abs welcome">
    <h2>Welcome to our site!<br>Our company provides a wide range of products</h2>
    <div class="feature" style="left:12px">
      <div class="img" role="img" aria-label="Seaside town with white houses" style="background:linear-gradient(180deg,#5aa7df 0%,#d8c9b0 50%,#1f5f8e 100%)"></div>
      <h3>Real Estate Development</h3>
      <p>Vestibulum iaculis nia est. Proin dictum<br>elementum velitsce euismod.</p>
      <a>Read More &gt;&gt;</a>
    </div>
    <div class="feature" style="left:197px">
      <div class="img" role="img" aria-label="Bowl of fresh vegetables" style="background:radial-gradient(circle,#e0643a 0%,#d6e6c0 50%,#7fc9a0 100%)"></div>
      <h3>Food &amp; Beverage</h3>
      <p>Vestibulum iaculis nia est. Proin dictum<br>elementum velitsce euismod.</p>
      <a>Read More &gt;&gt;</a>
    </div>
    <div class="feature" style="left:380px">
      <div class="img" role="img" aria-label="Commuter beside a tram on a city street" style="background:linear-gradient(90deg,#b9c0a0 0%,#d8d2c4 60%,#ece4dc 100%)"></div>
      <h3>Transportation</h3>
      <p>Vestibulum iaculis nia est. Proin dictum<br>elementum velitsce euismod.</p>
      <a>Read More &gt;&gt;</a>
    </div>
  </section>

  <footer class="abs footer">
    <div class="fcol" style="left:79px">
      <h4 style="border:none">Most Viewed Products</h4>
      <div class="grid">
        <span role="img" aria-label="Grilled food" style="background:#9a5a3a"></span>
        <span role="img" aria-label="Fresh produce" style="background:#c86a3a"></span>
        <span role="img" aria-label="Brick building" style="background:#8a6a5a"></span>
        <span role="img" aria-label="Winding road" style="background:#6f8a5a"></span>
        <span role="img" aria-label="Mountain house" style="background:#6a80a0"></span>
        <span role="img" aria-label="Townhouse" style="background:#a58a7a"></span>
        <span role="img" aria-label="Fruit" style="background:#d8a050"></span>
        <span role="img" aria-label="Portrait" style="background:#8ab8d0"></span>
        <span role="img" aria-label="Snowy village" style="background:#c8ccd4"></span>
      </div>
    </div>
    <div class="fcol" style="left:226px">
      <h4>Recent News</h4>
      <div class="news" style="margin-top:8px">Lorumipsum News!</div>
      <div class="news" style="font-size:5.5px;color:#bcd4ea;margin-top:7px">Tue, April 19, 2011</div>
      <div class="news" style="margin-top:3px">Pixel Harbor is excited to the shg<br>release Port Aldren to the Storely<br>Theme Store! We know.........</div>
      <div style="border-top:1px solid #2d7fc2;width:120px;margin-top:10px;padding-top:10px"><span class="fbtn">View More News</span></div>
    </div>
    <div class="fcol" style="left:376px">
      <h4>Contact Us</h4>
      <div class="news" style="margin-top:6px">5th Avenue dummy<br>1234 Linden Avenue<br>Port Aldren, dummy text123456<br>email-dummy@mailbox.example</div>
    </div>
    <div class="fcol" style="left:525px">
      <h4 style="border:none">Subscribe to Newsletter</h4>
      <div class="news" style="margin-top:4px">Email:</div>
      <div class="input"></div>
      <div style="text-align:right;width:120px;margin-top:9px"><span class="fbtn">Subscribe</span></div>
    </div>
    <div class="abs copy">© 2014 All Rights Reserved.</div>
  </footer>

</div>
</body>
</html>
```